Road Construction Company needs business cards

We would like a new business card designed for our business.

We're a road construction company based in Qld, Australia.

Can the business card please have the following information on it.

Name: Warren Halbeck
Position: General Manager
Phone: 0472 915 348
Email: Warren.halbeck@tovrin.com.au
Address: 87 Marrow Ave, Pendlebay, QLD, 4023
Website: www.tovrin.com.au

Visually we'd like the card to be professional and simple.

Attached is our logo.

Our website is www.tovrin.com.au

Target Market(s)

Men aged 25-60

Contact Information for Business Card

As listed in project description

Font styles to use
Serif

Requirements
Must have
• Large logo on back of card

```html
<!DOCTYPE html>
<html lang="en">
<head>
<meta charset="utf-8">
<title>Tovrin Business Card</title>
<link rel="stylesheet" href="https://fonts.googleapis.com/css2?family=Old+Standard+TT:wght@400;700&display=swap">
<style>
  :root {
    --page-bg: #e4e4e5;
    --card-white: #ffffff;
    --ink-navy: #24344f;
    --brand-blue: #2562ad;
    --icon-blue: #2a9fd6;
    --text-dark: #2b2b2b;
    --steel-light: #dcdde0;
    --steel-mid: #b4b6bb;
    --steel-dark: #86878c;
  }
  * { box-sizing: border-box; margin: 0; padding: 0; }
  html, body {
    width: 1200px;
    height: 900px;
    overflow: hidden;
    background: var(--page-bg);
    font-family: "Old Standard TT", Georgia, serif;
  }
  .sheet {
    width: 1200px;
    height: 900px;
    display: flex;
    align-items: center;
    justify-content: center;
    gap: 40px;
  }
  .card {
    position: relative;
    width: 540px;
    height: 308px;
    background: var(--card-white);
    overflow: hidden;
  }

  /* Front */
  .card-front .identity {
    position: absolute;
    top: 84px;
    left: 0;
    right: 0;
    text-align: center;
  }
  .identity .person-name {
    font-weight: 700;
    font-size: 29px;
    letter-spacing: 0.5px;
    color: var(--ink-navy);
    line-height: 1.05;
  }
  .identity .person-role {
    font-size: 20px;
    color: var(--brand-blue);
    line-height: 1.2;
  }
  .contact-list {
    position: absolute;
    left: 22px;
    top: 192px;
    list-style: none;
  }
  .contact-list li {
    display: flex;
    align-items: center;
    gap: 8px;
    height: 20px;
    font-size: 14.5px;
    color: var(--text-dark);
  }
  .contact-list li.web { font-size: 16.5px; }
  .contact-list svg {
    width: 15px;
    height: 15px;
    flex: none;
    stroke: var(--icon-blue);
    fill: none;
    stroke-width: 1.6;
    stroke-linecap: round;
    stroke-linejoin: round;
  }
  .front-wordmark {
    position: absolute;
    right: 16px;
    top: 232px;
    font-weight: 700;
    font-size: 22px;
    letter-spacing: 1.5px;
    color: var(--steel-mid);
  }
  .steel-bands {
    position: absolute;
    left: 0;
    right: 0;
    bottom: 8px;
  }
  .steel-bands .band {
    height: 7px;
    margin-top: 6px;
    background: linear-gradient(to right, rgba(220,221,224,0) 0%, var(--steel-light) 30%, var(--steel-mid) 70%, var(--steel-dark) 100%);
  }

  /* Back */
  .card-back {
    background: linear-gradient(to right, var(--card-white) 35%, #e9eaec 55%, #cfd0d4 80%, #b3b4b9 100%);
    display: flex;
    align-items: center;
    justify-content: center;
  }
  .back-wordmark {
    font-weight: 700;
    font-size: 66px;
    letter-spacing: 4px;
    color: var(--brand-blue);
    margin-top: -6px;
  }
</style>
</head>
<body>
<main class="sheet">
  <section class="card card-front" aria-label="Business card front">
    <div class="identity">
      <h1 class="person-name">WARREN HALBECK</h1>
      <p class="person-role">General Manager</p>
    </div>
    <ul class="contact-list">
      <li>
        <svg viewBox="0 0 16 16" aria-hidden="true"><path d="M3.5 1.8l2.3 2.6-1.4 1.8c.9 2 2.6 3.7 4.6 4.6l1.8-1.4 2.6 2.3-1.4 2C7.5 13.4 2.6 8.5 1.5 3.2z"/></svg>
        0472 915 348
      </li>
      <li>
        <svg viewBox="0 0 16 16" aria-hidden="true"><circle cx="8" cy="8" r="6.8"/><circle cx="8" cy="8" r="2.5"/><path d="M10.5 6v3c0 1.3 2 1.3 2 0"/></svg>
        Warren.halbeck@tovrin.com.au
      </li>
      <li>
        <svg viewBox="0 0 16 16" aria-hidden="true"><path d="M8 15s5-5 5-8.5a5 5 0 0 0-10 0C3 10 8 15 8 15z"/><circle cx="8" cy="6.5" r="1.8"/></svg>
        87 Marrow Ave, Pendlebay, QLD, 4023
      </li>
      <li class="web">
        <svg viewBox="0 0 16 16" aria-hidden="true"><circle cx="8" cy="8" r="6.8"/><ellipse cx="8" cy="8" rx="2.8" ry="6.8"/><path d="M1.2 8h13.6"/></svg>
        www.tovrin.com.au
      </li>
    </ul>
    <div class="front-wordmark">TOVRIN</div>
    <div class="steel-bands" aria-hidden="true">
      <div class="band"></div>
      <div class="band"></div>
    </div>
  </section>

  <section class="card card-back" aria-label="Business card back">
    <div class="back-wordmark">TOVRIN</div>
  </section>
</main>
</body>
</html>
```